Bright and beautiful business card for a coach

I'm a personal and business coach based in Perth, Australia. I need a business card that whilst subtle and elegant, will stand out and appeal on a table full of cards.

My business name is Fern Mentoring and the business card must represent the warmth and brightness implied in the name, without being gimmicky. It must have a warmth and appeal and be easy to read.

I prefer clean, minimalist designs.

It must align with the feel of my website and socials: https://www.fernmentoring-example.com.au/
https://www.instagram.com/fernmentoringau/
https://www.facebook.com/fernmentoringau
Updates

Hi Designers Thank you so much for taking the time to submit designs. I wonder if I could have explained myself a little better. Most of the designs that have been submitted look rather formal and many have quite corporate looking embellishments on them (to my eye). I would like softer, warmer, more organic. I’m open to people playing about and being more abstract, using softer embellishments (e.g the line drawing flowers and grasses I’ve used in my socials) incorporating other colours from my palette or like the social icons in my email signature (in PDF), perhaps playing with size/oversize, playing with the bleed. Please don’t be constrained by what I’ve already done, it merely needs to compliment. I’m sorry if I’m not using the right words or have led you astray. I’m no designer, but I’ve done my website, socials, email signature etc all myself (my logo was a design contest) and I was really hoping for my business card to be something more creative than I could have made with a template. Reminder: No black cards/sides please. Thank you 😊

Target Market(s)

Individuals, most likely but not all female. Creative thinkers. Likely professionals.

Industry/Entity Type

Business & Personal Coach

Contact Information for Business Card

(Fern Mentoring Logo) Name: Greta Pellham; Title: Business & Personal Coach; Phone number: +61 (0)458 913307; Email: greta@fernmentoring-example.com.au; Website: https://fernmentoring-example.com.au; Social icons for Facebook, Instagram & LinkedIn: @fernmentoringAU. Optional strapline: "A thinking partner to help you cut through the noise"

Font styles to use
Sans Serif

Colors
00AB8E
00BBA5
67D7C9
C6EFE9
E9F9F6
59FF00
82FF00
B8FF75
E3FFCB
F4FFEA
FFC000
F8CF3A
FAE287
FDF2CF
FEFAEE

Requirements
Must have
• Must align with feel of my website and socials. Must have a pop of #FFC000 (possibly whole of one side, or at least a block). Bright or white background. Easy to read.
Nice to have
• Possibly incorporate the sunshine/grass picture I have used in website and socials - will upload.
Should not have
• Must not be black or dark. Not impersonal or corporate looking.

```html
<!DOCTYPE html>
<html lang="en">
<head>
<meta charset="utf-8">
<title>Fern Mentoring – Business Card</title>
<link rel="stylesheet" href="https://fonts.googleapis.com/css2?family=Lato:wght@400;700&family=Montserrat:wght@500&family=Ms+Madi&display=swap">
<style>
  :root {
    --sun: #FFC000;
    --ink: #1f1f1f;
    --rule: #cfcfcf;
    --paper: #ffffff;
    --backdrop: #ecece8;
    --grass-deep: #3f5a1e;
    --grass: #6f8f2c;
  }
  * { box-sizing: border-box; margin: 0; padding: 0; }
  html, body { width: 1200px; height: 1015px; overflow: hidden; }
  body {
    background: var(--backdrop);
    font-family: "Lato", sans-serif;
    position: relative;
  }
  .card {
    position: absolute;
    left: 280px;
    width: 640px;
    height: 366px;
    overflow: hidden;
    box-shadow: 0 6px 18px rgba(0,0,0,.12);
  }
  .card--front { top: 111px; }
  .card--back { top: 537px; background: var(--paper); }

  /* front */
  .front-photo {
    position: absolute; inset: 0 0 58px 0;
    background:
      radial-gradient(circle at 38% 18%, rgba(255,236,190,.95) 0, rgba(243,217,168,.6) 12%, rgba(180,150,90,.25) 30%, transparent 50%),
      linear-gradient(180deg, #8a7a55 0%, var(--grass) 45%, var(--grass-deep) 100%);
  }
  .front-brand {
    position: absolute; left: 0; right: 0; top: 122px; text-align: center;
    color: #fff; font-family: "Montserrat", sans-serif; font-weight: 500;
    font-size: 38px; letter-spacing: 3px;
  }
  .front-band {
    position: absolute; left: 0; right: 0; bottom: 0; height: 58px;
    background: var(--sun);
    display: flex; justify-content: center; align-items: center; gap: 6px;
  }
  .social-dot { width: 28px; height: 28px; border-radius: 50%; background: var(--ink); }

  /* back */
  .back-brand {
    position: absolute; left: 24px; width: 270px; top: 154px; text-align: center;
    color: var(--sun); font-family: "Montserrat", sans-serif; font-weight: 500;
    font-size: 27px; letter-spacing: 1.5px; white-space: nowrap;
  }
  .divider { position: absolute; left: 312px; top: 86px; width: 1px; height: 150px; background: var(--rule); }
  .contact { position: absolute; left: 334px; top: 70px; }
  .contact__name { font-family: "Ms Madi", cursive; color: var(--sun); font-size: 42px; line-height: 1; }
  .contact__title { font-size: 16px; color: var(--ink); margin-top: 4px; }
  .contact__list { list-style: none; margin-top: 16px; }
  .contact__list li { display: flex; align-items: center; gap: 9px; font-size: 14px; color: var(--ink); line-height: 24px; white-space: nowrap; }
  .contact__list svg { width: 15px; height: 15px; flex: none; }
  .back-band { position: absolute; left: 0; right: 0; bottom: 0; height: 52px; background: var(--sun); }
  .strapline {
    position: absolute; left: 40px; right: 40px; bottom: 16px; text-align: center;
    font-family: "Ms Madi", cursive; font-size: 30px; color: var(--ink); line-height: 1; white-space: nowrap;
  }
</style>
</head>
<body>
  <section class="card card--front">
    <div class="front-photo" role="img" aria-label="Photo of sunlit grass at golden hour, sun glowing through soft blur"></div>
    <div class="front-brand">Fern Mentoring</div>
    <div class="front-band">
      <span class="social-dot"></span><span class="social-dot"></span><span class="social-dot"></span>
    </div>
  </section>

  <section class="card card--back">
    <div class="back-brand">Fern Mentoring</div>
    <div class="divider"></div>
    <div class="contact">
      <div class="contact__name">Greta Pellham</div>
      <div class="contact__title">Business &amp; Personal Coach</div>
      <ul class="contact__list">
        <li><svg viewBox="0 0 16 16"><path d="M3 1.5l3 .5 1 3-2 1.5a8 8 0 0 0 4.5 4.5L11 9l3 1 .5 3-2 1.5C7 14 2 9 1.5 3.5z" fill="var(--sun)"/></svg>+61 (0)458 913307</li>
        <li><svg viewBox="0 0 16 16"><rect x="1" y="3" width="14" height="10" fill="var(--sun)"/><path d="M1 3l7 6 7-6" fill="none" stroke="#fff" stroke-width="1.2"/></svg>greta@fernmentoring-example.com.au</li>
        <li><svg viewBox="0 0 16 16" fill="none" stroke="var(--sun)" stroke-width="1.3"><circle cx="8" cy="8" r="6.5"/><ellipse cx="8" cy="8" rx="3" ry="6.5"/><path d="M1.5 8h13M2.5 5h11M2.5 11h11"/></svg>www.fernmentoring-example.com.au</li>
      </ul>
    </div>
    <div class="back-band"></div>
    <p class="strapline">A thinking partner to help you cut through the noise</p>
  </section>
</body>
</html>
```